Tuition Center Website

We need a new web site for a tutoring company based in sydney.

We only teach senior highschool students and pride ourselves on building the students abilities to think their way through life.

I would like a bright and vibrant website that looks professional and modern.
It needs to look simple and neat but also have the functionality we need.
Images and flash would be good.

Please keep in mind that the site must be appealing to a younger audience.

We need a multipage website with the following navigation bars:

1.Home (As logo not "home" button)
I would like a news box/ticker somewhere that can stream our chatterbook and pipstream feeds and also any news updates we want to put up.
Subscribe to newsletter button.

2. About us.
This needs to be a pull down into:
-What we do
-Why we do it
-How we do it

3. Courses
Pulldown into:
-Maths
-English
-Science
(we may need to attach extra pages behind these e.g. Courses/Science/Physics or Courses/Science/Chemistry and possibly add a link to a new zandlo form)

4. Inspired
This page is like a blog page where we can upload videos, links to articles that we find to be inspiring and hopefully will inspire others.

5. Inspire
This is a recruitment page. Only content here.

6. Contact us.
Mapquill map widget and a 'contact us' form

* Our branding requires green close to #12FF3D

***Please have a look at the current website.
@ www.velmorlearning.com.au

Thanks everybody hope the revision of my brief is better and more informative than my last one

Target Market(s)

senior highschool students aged 15-19, parents ( to a lesser degree)

Industry/Entity Type

It Company

Requirements
Must have
• Ability to change content on pages.

The green doesn't have to be everywhere, but it must be obvious that it is our colour.

Nice to have
• Sites with a nicer mix of images and flash will be given more consideration. But then again, if you amaze us, you amaze us and we will go with your design.
Should not have
• Should stay away from ocre, brown colours and serif fonts.

```html
<!DOCTYPE html>
<html lang="en">
<head>
<meta charset="utf-8">
<title>Velmor Learning</title>
<link rel="stylesheet" href="https://fonts.googleapis.com/css2?family=Oswald:wght@400&family=Cabin:wght@400;500&family=Arimo:ital,wght@0,400;0,700;1,400&display=swap">
<style>
:root{
  --lime:#62e000;
  --brand:#4fc800;
  --brand-light:#9af55a;
  --ink:#333;
  --grey-text:#666;
  --head-grey:#5a5a5a;
  --link:#2a9ad6;
  --dark:#3a3a3a;
}
*{margin:0;padding:0;box-sizing:border-box}
html,body{width:1158px;height:1200px;overflow:hidden}
body{background:var(--lime);font-family:"Arimo",Arial,sans-serif;color:var(--ink);position:relative}
h2,h3{font-weight:400}
.utility-links{position:absolute;top:50px;right:172px;font-size:10px;color:#2c6a00;white-space:nowrap}
.utility-links span{margin:0 4px;color:#3f8a00}
.page{position:absolute;left:154px;top:70px;width:850px;height:1094px;background:#fff;border-radius:9px;overflow:hidden}
.header{height:83px;position:relative;border-bottom:1px solid #e2e2e2}
.logo{position:absolute;left:24px;top:22px}
.logo-name{font-family:"Cabin",sans-serif;font-size:29px;font-weight:500;color:var(--brand);letter-spacing:-.5px;line-height:1}
.logo-tag{font-size:9px;color:#222;margin-top:3px}
.nav{position:absolute;left:289px;top:0;height:83px;display:flex}
.nav a{font-family:"Oswald",sans-serif;font-size:12px;color:#444;text-decoration:none;padding:50px 11px 0;height:83px;text-transform:uppercase;letter-spacing:-.2px;line-height:1;display:flex;align-items:center}
.nav a.active{background:linear-gradient(#fff 0%,var(--brand-light) 40%,var(--brand) 100%);color:#1d4b00;padding:50px 12px 0}
.hero{height:312px;position:relative;background:linear-gradient(135deg,#6b4a32,#c6946b 35%,#3a2b24 60%,#a77f63 80%,#2a211d)}
.hero-arrow{position:absolute;top:130px;width:28px;height:52px;background:#bbb;border:2px solid #ddd}
.hero-arrow.prev{left:-2px;border-radius:0 26px 26px 0}
.hero-arrow.next{right:-2px;border-radius:26px 0 0 26px}
.hero-arrow svg{position:absolute;top:17px}
.hero-band{position:absolute;left:0;bottom:0;width:100%;height:74px;background:rgba(20,20,20,.82);display:flex;align-items:center}
.hero-title{font-family:"Oswald",sans-serif;font-size:27px;color:#fff;line-height:1.05;margin-left:35px;width:140px}
.hero-copy{font-size:9.5px;color:#eee;width:440px;line-height:1.3}
.hero-copy b{font-weight:400;font-size:10.5px;display:block}
.enquire{position:absolute;right:12px;top:15px;width:216px;height:40px;background:var(--brand);color:#0b2a00;font-size:21px;display:flex;align-items:center;justify-content:center;letter-spacing:.5px}
.intro{height:247px;position:relative}
.section-title{font-family:"Cabin",sans-serif;font-size:25px;color:var(--head-grey);position:absolute;top:17px}
.photo{position:absolute;background:linear-gradient(160deg,#c99b76,#4a3428 55%,#221a16)}
.body-copy{position:absolute;font-size:9.4px;line-height:13.6px;color:var(--grey-text);text-align:justify}
.btn{position:absolute;height:29px;background:linear-gradient(#4c4c4c,#2a2a2a);color:#fff;font-family:"Cabin",sans-serif;font-size:12.5px;display:flex;align-items:center;justify-content:center;border-radius:2px}
.blog-arrows{position:absolute;right:35px;top:27px;display:flex;gap:12px}
.feature{height:263px;position:relative;background:linear-gradient(#e2e2e2,#efefef 60%,#e4e4e4);border-top:1px solid #ccc}
.col-title{font-family:"Oswald",sans-serif;font-size:16px;color:#555;position:absolute;top:19px;letter-spacing:-.2px}
.quote{position:absolute;left:34px;width:249px;height:87px;background:#fff;border:1px solid #c9c9c9;box-shadow:0 1px 2px rgba(0,0,0,.15)}
.quote .avatar-cell{position:absolute;left:0;top:0;width:66px;height:100%;border-right:1px solid #ddd;background:#f6f6f6}
.quote .avatar{position:absolute;left:10px;top:20px;width:46px;height:46px;border:1px solid #bbb;background:#fff;padding:4px}
.quote .avatar div{width:100%;height:100%;background:linear-gradient(#cfd9e3,#8aa0b5)}
.quote p{position:absolute;left:77px;top:12px;width:168px;font-size:9.5px;line-height:10.3px;color:#444}
.quote .name{position:absolute;left:77px;top:65px;font-size:9.5px;font-weight:700;color:#333}
.news{position:absolute;left:316px;width:200px;font-size:9.8px;line-height:15px;color:#555}
.news a{color:var(--link);text-decoration:none}
.news em{color:#333}
.trial-icon{position:absolute;left:541px;top:57px;width:51px;height:46px;background:var(--brand)}
.trial-copy{position:absolute;left:604px;top:54px;width:220px;font-size:9.8px;line-height:13.5px;color:#555;text-align:justify}
.contact-lines{position:absolute;left:540px;top:203px;font-size:9.8px;line-height:13.6px;color:#555}
.partners{height:120px;position:relative}
.partners-title{position:absolute;left:34px;top:28px;font-family:"Cabin",sans-serif;font-size:25px;line-height:30px;color:var(--head-grey)}
.partners-divider{position:absolute;left:150px;top:8px;width:12px;height:112px;background:linear-gradient(90deg,rgba(0,0,0,.12),rgba(0,0,0,0))}
.partner-badge{position:absolute;background:#c9c9c9;border-radius:3px}
.footer{height:69px;position:relative;background:linear-gradient(#5a5a5a,#2c2c2c)}
.footer-links{position:absolute;left:34px;top:20px;font-size:10.5px;line-height:17px;color:#eee}
.social-label{position:absolute;right:158px;top:30px;font-size:10.5px;color:#eee}
.social{position:absolute;right:26px;top:20px;display:flex;gap:4px}
.social span{width:26px;height:26px;border-radius:50%;background:#fff}
</style>
</head>
<body>
<nav class="utility-links">Past Exam Papers<span>|</span>State Students Online<span>|</span>Admissions Centre<span>|</span>Exam Online [Study Resources]<span>|</span>Help for Study Stress<span>|</span>Velmor on Chatterbook</nav>

<div class="page">
  <header class="header">
    <div class="logo">
      <div class="logo-name">velmor learning</div>
      <div class="logo-tag">think clearly, learn boldly, aim higher</div>
    </div>
    <nav class="nav">
      <a class="active">Home</a><a>About Us</a><a>Find Us</a><a>Get in Touch</a><a>Recent News</a><a>Year 10 Classes</a><a>Yr 11 &amp; 12 HSC Classes</a>
    </nav>
  </header>

  <section class="hero" role="img" aria-label="Photo of a group of smiling graduating students in gowns">
    <div class="hero-arrow prev"><svg width="12" height="14" style="left:6px"><path d="M10 0v14L0 7z" fill="#eee"/></svg></div>
    <div class="hero-arrow next"><svg width="12" height="14" style="left:8px"><path d="M0 0v14l10-7z" fill="#eee"/></svg></div>
    <div class="hero-band">
      <div class="hero-title">BE<br>CURIOUS.</div>
      <p class="hero-copy"><b>REAL HSC COACHING &amp; MENTORING.</b>The HSC help you need, in the years you need it. We offer small classes, individualised attention and genuine care for each student. It's different - in a good way. Feel free to find out more about us, and let us know if there's any way we can help you on your journey.</p>
      <div class="enquire">ENQUIRE NOW</div>
    </div>
  </section>

  <section class="intro">
    <h2 class="section-title" style="left:34px">Welcome to Our Site</h2>
    <div class="photo" style="left:34px;top:64px;width:184px;height:164px" role="img" aria-label="Photo of smiling students in graduation gowns"></div>
    <p class="body-copy" style="left:234px;top:62px;width:265px">At vero eos et accusamus et iusto odio dignissimos ducimus qui blanditiis praesentium voluptatum deleniti atque corrupti quos dolores etquas molestias excepturi sint occaecati cupiditate non provident, similique sunt in culpa qui officia deserunt mollitia animi, iiilaborum et dolorum fuga. Et harum quidem rerum facilis est et expedita distinctio.Nam libero tempore, cum soluta nobis est eligendi optio cumque nihil impedit quo minus id quod maxime placeat facere possili,</p>
    <div class="btn" style="left:234px;top:199px;width:93px">View More</div>

    <h2 class="section-title" style="left:530px">Our Blog</h2>
    <div class="blog-arrows"><svg width="8" height="11"><path d="M7 0L1 5.5 7 11" stroke="#222" stroke-width="2" fill="none"/></svg><svg width="8" height="11"><path d="M1 0l6 5.5L1 11" stroke="#222" stroke-width="2" fill="none"/></svg></div>
    <div class="photo" style="left:531px;top:63px;width:90px;height:64px;background:linear-gradient(#e8eef3,#b9c4cc)" role="img" aria-label="Photo of a smiling blog author"></div>
    <p class="body-copy" style="left:633px;top:62px;width:185px">At vero eos et accusamus et iusto odio dignissimos ducimus qui blanditiis prae-sentium voluptatum deleniti atque corrupti quos dolores etquas molestias excepturi sint occaecati cupiditate non</p>
    <p class="body-copy" style="left:531px;top:130px;width:287px">At vero eos et accusamus et iusto odio dignissimos ducimus qui blanditiis praesentium voluptatum deleniti atque corrupti quos dolores etquas molestias excepturi sint occaecati cupiditate non provident, similique sunt in culpaest et expedita distinctio.</p>
    <div class="btn" style="left:530px;top:199px;width:93px">View More</div>
  </section>

  <section class="feature">
    <h3 class="col-title" style="left:34px">What Our Students Say.</h3>
    <div class="quote" style="top:56px">
      <div class="avatar-cell"><div class="avatar"><div></div></div></div>
      <p>Lorem ipsum dolor sit m,conipiscing elit. Etiam commodo ante non neque bibendum tristique. Vestibulum nulla diam, egestas in imperdiet sed, .</p>
      <div class="name">John Doe</div>
    </div>
    <div class="quote" style="top:151px">
      <div class="avatar-cell"><div class="avatar"><div></div></div></div>
      <p>Lorem ipsum dolor sit m,conipiscing elit. Etiam commodo ante non neque bibendum tristique. Vestibulum nulla diam, egestas in imperdiet sed, .</p>
      <div class="name">John Doe</div>
    </div>

    <h3 class="col-title" style="left:316px">Recent News.</h3>
    <div class="news" style="top:53px">Lorem ipsum dolor sit amet, consectetuer adipiscing elit, sed diam nonummy nibh<br><a>http://vlm.to/trg87z</a><br><em>24 minutes ago</em></div>
    <div class="news" style="top:119px">Lorem ipsum dolor sit amet, consectetuer adipiscing elit, sed diam nonummy nibh<br><a>http://vlm.to/trg87z</a><br><em>24 minutes ago</em></div>
    <div class="news" style="top:184px">Lorem ipsum dolor sit amet, consectetuer adipiscing elit, sed diam nonummy nibh<br><a>http://vlm.to/trg87z</a><br><em>24 minutes ago</em></div>

    <h3 class="col-title" style="left:540px">Ask for your free trial lesson.</h3>
    <div class="trial-icon" role="img" aria-label="Illustration of a chalkboard"></div>
    <p class="trial-copy">Because we believe you shouldn't have to sign up until you see what it's actually like. Call or email us now!</p>
    <div class="btn" style="left:541px;top:116px;width:121px">Send an Enquiry</div>
    <h3 class="col-title" style="left:540px;top:172px">Contact Us.</h3>
    <div class="contact-lines">Street: 48 Larkin Rd Brenfield NSW 2199<br>Phone: (02) 5550 1457<br>Email: learn@velmorlearning.com.au</div>
  </section>

  <section class="partners">
    <h2 class="partners-title">Our<br>Partners</h2>
    <div class="partners-divider"></div>
    <div class="partner-badge" style="left:195px;top:50px;width:80px;height:26px"></div>
    <div class="partner-badge" style="left:344px;top:42px;width:114px;height:44px;background:#dcdcdc"></div>
    <div class="partner-badge" style="left:535px;top:52px;width:68px;height:22px"></div>
    <div class="partner-badge" style="left:683px;top:52px;width:66px;height:22px;background:#e8c97a"></div>
  </section>

  <footer class="footer">
    <div class="footer-links">Privacy Policy | Terms of Services | Sitemap<br>© Copyright 2013 All rights reserved.</div>
    <div class="social-label">Social Media:</div>
    <div class="social"><span title="chatterbook"></span><span></span><span title="pipstream"></span><span title="Mapquill"></span></div>
  </footer>
</div>
</body>
</html>
```